Business card design for Automotive workshop

We need a business card for a new automotive repair and tyre shop called Keelstone Prime Automotive located in New Zealand. We are a clean, modern and fresh workshop and company.

Front needs to feature logo,
my name:
Marlo Fenwicke (director)

Address:
48 Tarn Lane
Rawena Bay 3592

Phone: 07 594 2713
Mobile: 027 451 9362
Email: office@keelstoneautomotive.example.nz
Website: keelstoneautomotive.example.nz

Back needs to feature an area to write down appointment details, date and time.

Also feature a list of jobs and work we do such as,
Vehicle Servicing
All Mechanical Repairs
Warrant of Fitness
Tyres & Wheel Alignments
Automotive Diagnostics
Automotive Parts & Supplies

```html
<!DOCTYPE html>
<html lang="en">
<head>
<meta charset="utf-8">
<title>Keelstone Prime Automotive – Business Card</title>
<link rel="stylesheet" href="https://fonts.googleapis.com/css2?family=Rubik:wght@400;500;700&display=swap">
<style>
  :root {
    --red: #e3141b;
    --ink: #1c1c1e;
    --card-dark: #1f1f21;
    --paper: #ffffff;
    --grey: #55575b;
    --stage: #d9dadc;
  }
  * { box-sizing: border-box; margin: 0; padding: 0; }
  html, body { width: 1200px; height: 800px; overflow: hidden; }
  body {
    background: var(--stage);
    font-family: "Rubik", Arial, sans-serif;
    display: flex;
    align-items: center;
    justify-content: center;
    gap: 40px;
  }
  .card {
    position: relative;
    width: 540px;
    height: 330px;
    border-bottom: 4px solid var(--red);
    box-shadow: 0 10px 24px rgba(0,0,0,.18);
    overflow: hidden;
  }

  /* Wordmark */
  .wordmark {
    display: flex;
    align-items: center;
    gap: 10px;
    font-weight: 700;
    color: var(--red);
    text-transform: uppercase;
    letter-spacing: .5px;
    line-height: 1.05;
  }
  .wordmark__square { width: 14px; height: 14px; background: var(--red); flex: none; }

  /* Front */
  .card--front { background: var(--paper); color: var(--ink); }
  .card--front .wordmark { position: absolute; top: 58px; left: 50%; transform: translateX(-50%); font-size: 26px; white-space: nowrap; }
  .front__rule { position: absolute; left: 120px; right: 34px; top: 214px; height: 1px; background: var(--ink); }
  .front__person { position: absolute; left: 34px; top: 168px; }
  .front__name { color: var(--red); font-size: 21px; font-weight: 500; }
  .front__role { font-size: 12px; font-weight: 500; margin-top: 14px; }
  .front__contact { position: absolute; left: 34px; top: 232px; list-style: none; font-size: 12.5px; line-height: 21px; color: var(--grey); }
  .front__contact li { display: flex; align-items: center; gap: 8px; }
  .front__contact svg { width: 12px; height: 12px; fill: var(--red); flex: none; }
  .front__address { position: absolute; right: 34px; top: 226px; text-align: right; font-size: 12.5px; line-height: 19px; color: var(--grey); font-style: normal; }
  .front__web { margin-top: 6px; font-size: 11.5px; }

  /* Back */
  .card--back { background: var(--card-dark); color: #fff; }
  .services { position: absolute; left: 250px; top: 28px; }
  .services__title { color: var(--red); font-size: 16px; font-weight: 700; text-transform: uppercase; margin-bottom: 4px; }
  .services__list { list-style: none; font-size: 13.5px; line-height: 20px; }
  .services__list li::before { content: "•"; color: var(--red); margin-right: 9px; }
  .card--back .wordmark { position: absolute; left: 28px; top: 96px; font-size: 19px; flex-wrap: nowrap; }
  .wordmark__text span { display: block; }
  .appointment {
    position: absolute; left: 28px; right: 28px; bottom: 26px; height: 100px;
    background: var(--paper); padding: 18px 22px;
    display: flex; flex-direction: column; justify-content: space-around;
  }
  .appointment__row { display: flex; align-items: baseline; gap: 6px; color: var(--red); font-size: 13px; }
  .appointment__line { flex: 1; border-bottom: 1.5px dotted var(--ink); }
</style>
</head>
<body>

  <section class="card card--front" aria-label="Card front">
    <div class="wordmark"><span class="wordmark__square"></span>Keelstone Prime Automotive</div>

    <div class="front__person">
      <p class="front__name">Marlo Fenwicke</p>
      <p class="front__role">Director</p>
    </div>
    <div class="front__rule"></div>

    <ul class="front__contact">
      <li><svg viewBox="0 0 24 24" aria-hidden="true"><path d="M6.6 10.8a15.1 15.1 0 0 0 6.6 6.6l2.2-2.2a1 1 0 0 1 1-.25 11.4 11.4 0 0 0 3.6.57 1 1 0 0 1 1 1V20a1 1 0 0 1-1 1A17 17 0 0 1 3 4a1 1 0 0 1 1-1h3.5a1 1 0 0 1 1 1c0 1.25.2 2.45.57 3.57a1 1 0 0 1-.25 1z"/></svg>07 594 2713</li>
      <li><svg viewBox="0 0 24 24" aria-hidden="true"><path d="M7 1h10a2 2 0 0 1 2 2v18a2 2 0 0 1-2 2H7a2 2 0 0 1-2-2V3a2 2 0 0 1 2-2zm0 3v14h10V4z"/></svg>027 451 9362</li>
      <li><svg viewBox="0 0 24 24" aria-hidden="true"><path d="M2 5h20v14H2zm2 2v.5l8 5 8-5V7l-8 5z"/></svg>office@keelstoneautomotive.example.nz</li>
    </ul>

    <address class="front__address">
      48 Tarn Lane<br>
      Rawena Bay 3592
      <p class="front__web">www.keelstoneautomotive.example.nz</p>
    </address>
  </section>

  <section class="card card--back" aria-label="Card back">
    <div class="services">
      <h2 class="services__title">Vehicle Servicing</h2>
      <ul class="services__list">
        <li>All Mechanical Repairs</li>
        <li>Warrant of Fitness</li>
        <li>Tyres &amp; Wheel Alignments</li>
        <li>Automotive Diagnostics</li>
        <li>Automotive Parts &amp; Supplies</li>
      </ul>
    </div>

    <div class="wordmark"><span class="wordmark__square"></span><span class="wordmark__text"><span>Keelstone Prime</span><span>Automotive</span></span></div>

    <div class="appointment">
      <div class="appointment__row">Date:<span class="appointment__line"></span>Time:<span class="appointment__line"></span></div>
      <div class="appointment__row">Date:<span class="appointment__line"></span>Time:<span class="appointment__line"></span></div>
    </div>
  </section>

</body>
</html>
```